Climbing Gear Company Stationary Design

We need some new stationary to standardise our business.
We require:

Business Card
A4 Letterhead
With complements slip

Our business is a Distributor and retailer of rock climbing equipment throughout Australia.
We need to the stationary (business card in particular) to reflect this.

Target Market(s)

customers, other retail outlets, overseas manufacturers.

Industry/Entity Type

Business

Requirements
Must have
• company logo
website url- www.ridgetopgearworks.com.au
email - mark@ridgetopgearworks.com
Business Address: Unit 3, 14-16 Marlowe Street, Harlow Bay, VIC, 2371
Phone: 0438 627 194
my Name (on Business card) - Gordon Pellimore
use of Blue colour in our logo

```html
<!DOCTYPE html>
<html lang="en">
<head>
<meta charset="utf-8">
<title>Ridgetop Gearworks – Business Card</title>
<link href="https://fonts.googleapis.com/css2?family=Source+Sans+3:wght@400;700&display=swap" rel="stylesheet">
<style>
  :root {
    --brand-blue: #1f3d80;
    --text-grey: #555a60;
    --divider: #c8c8c8;
    --card: #ffffff;
    --backdrop: #eeeeee;
    --swoosh-light: #e6e6e6;
    --swoosh-dark: #111111;
  }
  html, body {
    margin: 0;
    padding: 0;
    width: 1200px;
    height: 483px;
    overflow: hidden;
    background: var(--backdrop);
    font-family: "Source Sans 3", Arial, sans-serif;
  }
  .stage { position: relative; width: 1200px; height: 483px; }
  .card {
    position: absolute;
    top: 103px;
    width: 523px;
    height: 300px;
    background: var(--card);
    overflow: hidden;
  }
  .card--front { left: 50px; }
  .card--back { left: 606px; }

  .brand { position: absolute; text-align: center; color: var(--brand-blue); }
  .brand__name {
    font-weight: 700;
    text-transform: uppercase;
    letter-spacing: 0.5px;
    line-height: 1;
    white-space: nowrap;
  }
  .brand__tagline {
    font-weight: 400;
    white-space: nowrap;
    line-height: 1;
  }
  .card--front .brand { top: 46px; left: 58px; width: 410px; }
  .card--front .brand__name { font-size: 38px; }
  .card--front .brand__tagline { font-size: 15px; margin-top: 10px; letter-spacing: 4.4px; }
  .card--back .brand { top: 128px; left: 98px; width: 330px; }
  .card--back .brand__name { font-size: 31px; }
  .card--back .brand__tagline { font-size: 12px; margin-top: 9px; letter-spacing: 3.4px; }

  .person-name {
    position: absolute;
    top: 151px;
    left: 0;
    width: 516px;
    text-align: center;
    color: var(--brand-blue);
    font-size: 17px;
  }
  .contact {
    position: absolute;
    top: 192px;
    font-size: 11.5px;
    line-height: 18px;
    color: var(--text-grey);
    white-space: nowrap;
  }
  .contact--address { right: 283px; text-align: right; }
  .contact--direct { left: 270px; }
  .contact-divider {
    position: absolute;
    top: 194px;
    left: 254px;
    width: 1px;
    height: 34px;
    background: var(--divider);
  }
  .footer-wave { position: absolute; left: 0; top: 0; }
  .footer-url {
    position: absolute;
    top: 271px;
    left: 90px;
    color: #ffffff;
    font-size: 11px;
  }
  .back-url {
    position: absolute;
    top: 202px;
    left: 0;
    right: 0;
    text-align: center;
    color: var(--text-grey);
    font-size: 14px;
    letter-spacing: 2.6px;
  }
</style>
</head>
<body>
<main class="stage">
  <section class="card card--front" aria-label="Business card front">
    <div class="brand">
      <div class="brand__name">Ridgetop Gearworks</div>
      <div class="brand__tagline">THE KIT•THE CLIMB•THE OUTDOORS</div>
    </div>
    <div class="person-name">Gordon Pellimore</div>
    <div class="contact contact--address">
      Unit 3, 14-16 Marlowe Street<br>
      Harlow Bay, VIC, 2371
    </div>
    <div class="contact-divider"></div>
    <div class="contact contact--direct">
      P : 0438 627 194<br>
      E : mark@ridgetopgearworks.com
    </div>
    <svg class="footer-wave" width="523" height="300" viewBox="0 0 523 300" aria-hidden="true">
      <defs>
        <linearGradient id="swoosh" x1="0" y1="0" x2="1" y2="0">
          <stop offset="0" stop-color="var(--swoosh-light)" stop-opacity="0.3"/>
          <stop offset="0.5" stop-color="#bdbdbd"/>
          <stop offset="1" stop-color="var(--swoosh-dark)"/>
        </linearGradient>
      </defs>
      <path d="M0,250 Q270,230 523,278 L523,290 Q270,243 0,259 Z" fill="url(#swoosh)"/>
      <path d="M0,259 Q270,243 523,290 L523,300 L0,300 Z" fill="var(--brand-blue)"/>
    </svg>
    <div class="footer-url">www.ridgetopgearworks.com.</div>
  </section>

  <section class="card card--back" aria-label="Business card back">
    <div class="brand">
      <div class="brand__name">Ridgetop Gearworks</div>
      <div class="brand__tagline">THE KIT•THE CLIMB•THE OUTDOORS</div>
    </div>
    <div class="back-url">www.ridgetopgearworks.com.</div>
  </section>
</main>
</body>
</html>
```